Veldmark Supplies Business Card

Professional business card that stand out to our potential customers. Front and back with clean modern design

Industry/Entity Type

Oil and gas

Contact Information for Business Card

Name, address, website , office phone and cell number

Requirements
Must have
• Editable files for each employee

```html
<!DOCTYPE html>
<html lang="en">
<head>
<meta charset="utf-8">
<title>Veldmark Supplies Business Card</title>
<link href="https://fonts.googleapis.com/css2?family=Roboto:wght@400;500;700;900&display=swap" rel="stylesheet">
<style>
  :root {
    --backdrop: #3b3b3d;
    --card-black: #1c1c1e;
    --brand-red: #d9141c;
    --deep-red: #a3100f;
    --brand-cyan: #1aa9d3;
    --ink-light: #ffffff;
    --ink-soft: #f1dede;
  }
  * { margin: 0; padding: 0; box-sizing: border-box; }
  html, body { width: 1200px; height: 694px; overflow: hidden; }
  body {
    background: var(--backdrop);
    font-family: "Roboto", Arial, sans-serif;
    position: relative;
  }
  .card {
    position: absolute;
    top: 197px;
    width: 520px;
    height: 300px;
    border-radius: 30px;
    background: var(--card-black);
    overflow: hidden;
  }
  .card-front { left: 50px; }
  .card-back { left: 630px; display: flex; }

  .brand {
    display: flex;
    align-items: center;
    gap: 12px;
    color: var(--ink-light);
    font-weight: 900;
    text-transform: uppercase;
    letter-spacing: 0.02em;
  }
  .brand-mark {
    display: block;
    background: var(--brand-red);
  }
  .card-front .brand {
    position: absolute;
    left: 50%;
    top: 50%;
    transform: translate(-50%, -50%);
    font-size: 34px;
    white-space: nowrap;
  }
  .card-front .brand-mark { width: 30px; height: 30px; }

  .back-brand-panel {
    width: 44%;
    display: flex;
    align-items: center;
    justify-content: center;
  }
  .back-brand-panel .brand {
    font-size: 18px;
    gap: 8px;
    flex-direction: column;
    text-align: center;
    line-height: 1.15;
  }
  .back-brand-panel .brand-mark { width: 22px; height: 22px; }

  .contact-panel {
    width: 56%;
    background: var(--deep-red);
    color: var(--ink-light);
    padding: 30px 26px 24px 28px;
  }
  .person-name { font-size: 27px; font-weight: 400; line-height: 1.1; }
  .person-role { font-size: 14px; font-weight: 500; margin-top: 2px; }
  .address { font-size: 14px; line-height: 1.3; margin-top: 14px; color: var(--ink-soft); }
  .contact-list { list-style: none; margin-top: 12px; }
  .contact-list li {
    display: flex;
    align-items: flex-start;
    gap: 10px;
    font-size: 14px;
    line-height: 1.3;
    margin-bottom: 7px;
    color: var(--ink-soft);
  }
  .contact-icon { width: 15px; height: 15px; flex: none; margin-top: 2px; }
</style>
</head>
<body>
  <section class="card card-front" aria-label="Card front">
    <div class="brand"><span class="brand-mark"></span>Veldmark Supplies</div>
  </section>

  <section class="card card-back" aria-label="Card back">
    <div class="back-brand-panel">
      <div class="brand"><span class="brand-mark"></span>Veldmark<br>Supplies</div>
    </div>
    <div class="contact-panel">
      <h1 class="person-name">Marcus Dellinger</h1>
      <p class="person-role">Owner</p>
      <p class="address">412 N Halvern Rd Suite 7,<br>Midland, TX 79705, United States</p>
      <ul class="contact-list">
        <li>
          <svg class="contact-icon" viewBox="0 0 16 16" fill="#fff"><path d="M3.5 1.5l2.5 0 1 3.5-1.8 1.2a9 9 0 0 0 4.6 4.6L11 9l3.5 1v2.5c0 1-1 2-2 2A11 11 0 0 1 1.5 3.5c0-1 1-2 2-2z"/></svg>
          (555)014-2287
        </li>
        <li>
          <svg class="contact-icon" viewBox="0 0 16 16" fill="none" stroke="#fff" stroke-width="1.5"><rect x="1.5" y="3.5" width="13" height="9"/><path d="M1.5 3.5l6.5 5 6.5-5"/></svg>
          sales@veldmarksupplies.com
        </li>
        <li>
          <svg class="contact-icon" viewBox="0 0 16 16" fill="none" stroke="#fff" stroke-width="1.4"><circle cx="8" cy="8" r="6.3"/><ellipse cx="8" cy="8" rx="2.8" ry="6.3"/><path d="M1.7 8h12.6"/></svg>
          www.veldmarksupplies.com
        </li>
        <li>
          <svg class="contact-icon" viewBox="0 0 16 16" fill="none" stroke="#fff" stroke-width="1.5"><circle cx="8" cy="9" r="5.5"/><path d="M8 6v3.2l2 1.3M2.5 3l2-1.5M13.5 3l-2-1.5"/></svg>
          <span>Monday – Friday<br>8:30am – 5pm</span>
        </li>
      </ul>
    </div>
  </section>
</body>
</html>
```